Webdesign für Vertrieb und Verkauf von Vellorix Produkten im Firmenbereich
Zielgruppe
Vertrieb und Verkauf von Vellorix Produkten im Firmenbereich (Vellorix KLT, Quorent Flowdesk)
Aufgabenstellung
Ein Logo gibt es auf der bestehenden Internetseite https://www.kelbrotech.eu/ - Dieses Logo bitte beibehalten.
Ansonsten eine schnörkelloses klares Design welches Firmenkunden anspricht und wo man sich schnell zurecht findet.

```html
<!DOCTYPE html>
<html lang="de">
<head>
<meta charset="utf-8">
<title>Kelbro – Kontakt</title>
<link href="https://fonts.googleapis.com/css2?family=Fira+Sans:wght@400;500;600;700&display=swap" rel="stylesheet">
<style>
:root{
  --brand:#a51c45;
  --ink:#111;
  --muted:#999;
  --line:#ddd;
  --footer:#000;
  --footer-box:#1b1b1b;
  --footer-bottom:#222;
  --white:#fff;
}
*{box-sizing:border-box;margin:0;padding:0}
html,body{width:1053px;height:1200px;overflow:hidden;background:var(--white);font-family:"Fira Sans",sans-serif;color:var(--ink)}
.page{position:relative;width:1053px;height:1200px}
.header{position:absolute;top:0;left:0;width:100%;height:55px;border-bottom:1px solid #eee;background:var(--white)}
.header .divider{position:absolute;top:0;width:1px;height:55px;background:#eee}
.brand{position:absolute;left:189px;top:0;width:69px;height:55px;display:flex;align-items:center;justify-content:center;gap:4px;font-size:13px;letter-spacing:1px;color:#555}
.brand .mark{width:8px;height:8px;background:var(--brand)}
.nav{position:absolute;right:240px;top:22px;display:flex;gap:14px;font-size:8px;font-weight:600}
.nav a{color:#333;text-decoration:none}
.nav a.active{color:var(--brand)}
.burger{position:absolute;left:853px;top:24px;width:11px}
.burger span{display:block;height:1px;background:#333;margin-bottom:2.5px}
.hero{position:absolute;top:55px;left:0;width:100%;height:194px;background:radial-gradient(ellipse at 50% 30%,#efc7d2 0%,#f1e6e9 30%,#eee 60%,#f6f6f6 100%)}
.hero h1{position:absolute;top:135px;width:100%;text-align:center;font-size:17px;font-weight:700}
.tab{position:absolute;top:246px;height:56px;background:var(--white);border-top:3px solid var(--brand);box-shadow:0 1px 4px rgba(0,0,0,.2);padding:31px 11px 0;font-size:12px;font-weight:700}
.contact{position:absolute;left:189px;top:0}
.row{position:absolute;left:0;display:flex;align-items:center;gap:11px;font-size:9px;white-space:nowrap}
.row svg{width:22px;height:22px;flex:none}
.form{position:absolute;left:532px;top:320px;width:333px}
.field{height:31px;border-bottom:1px solid var(--line);font-size:9px;color:var(--muted);padding-top:10px}
.field.area{height:150px}
.send{position:absolute;left:0;top:246px;width:53px;height:25px;background:#000;color:var(--white);font-size:9px;font-weight:600;display:flex;align-items:center;justify-content:center}
.map{position:absolute;top:641px;left:0;width:100%;height:276px;background:linear-gradient(160deg,#f2f2f2,#e6e6e6)}
.footer{position:absolute;top:917px;left:0;width:100%;height:219px;background:var(--footer);color:var(--white)}
.about{position:absolute;left:189px;top:-5px;width:327px;height:159px;background:var(--footer-box);border-top:5px solid var(--brand);padding:30px 22px;color:#bbb;font-size:9px;line-height:14px}
.about .logo{font-size:15px;letter-spacing:1px;color:#ddd;margin-bottom:12px;display:flex;align-items:center;gap:6px}
.about .logo span{width:9px;height:9px;background:#ddd}
.col{position:absolute;top:36px;font-size:9px}
.col h4{font-size:9px;font-weight:600;margin-bottom:20px}
.social li{list-style:none;display:flex;align-items:center;gap:9px;margin-bottom:5px}
.social i{width:21px;height:21px;background:#1b1b1b;display:block}
.links a{display:block;color:var(--white);text-decoration:none;font-weight:600;padding:4px 0 6px;border-bottom:1px solid #222;width:94px}
.contact-col p{line-height:14px;margin-bottom:14px}
.bottom{position:absolute;top:1136px;left:0;width:100%;height:64px;background:var(--footer-bottom);color:var(--white);font-size:8px}
.bottom p{position:absolute;left:189px;top:31px}
.bottom a{color:var(--white)}
.totop{position:absolute;left:839px;top:22px;width:26px;height:25px;border:1px solid #666;display:flex;align-items:center;justify-content:center}
</style>
</head>
<body>
<div class="page">
  <header class="header">
    <div class="divider" style="left:258px"></div>
    <div class="divider" style="left:834px"></div>
    <div class="brand"><span class="mark"></span>KELBRO</div>
    <nav class="nav"><a href="#">Home</a><a href="#">Was ist Vellorix KLT?</a><a href="#">Meine Vorteile</a><a class="active" href="#">Kontakt</a></nav>
    <div class="burger"><span></span><span></span><span></span></div>
  </header>

  <section class="hero" role="img" aria-label="Heller Hintergrund mit rosa Telefonhörer und Handschlag-Motiv">
    <h1>Kontakt</h1>
  </section>

  <div class="tab" style="left:189px">Kontaktdaten:</div>
  <div class="tab" style="left:532px">Kontaktformular:</div>

  <section class="contact">
    <div class="row" style="top:325px"><svg viewBox="0 0 22 22" fill="none" stroke="#a51c45" stroke-width="1"><path d="M11 20s-6-7-6-11a6 6 0 0 1 12 0c0 4-6 11-6 11z"/><circle cx="11" cy="8.5" r="1.6"/></svg>Kelbro GmbH Lindenweg 14 - 90411 Nürnberg</div>
    <div class="row" style="top:371px"><svg viewBox="0 0 22 22" fill="none" stroke="#a51c45" stroke-width="1"><path d="M4 12a7 7 0 0 1 14 0"/><rect x="2" y="11" width="3" height="5"/><rect x="17" y="11" width="3" height="5"/><path d="M18 16c0 3-3 4-6 4"/></svg>+49 911 55 20 31 40</div>
    <div class="row" style="top:406px"><svg viewBox="0 0 22 22" fill="none" stroke="#a51c45" stroke-width="1"><rect x="6" y="2" width="10" height="6"/><rect x="2" y="8" width="18" height="8"/><rect x="6" y="13" width="10" height="7"/><path d="M8 16h6M8 18h6"/></svg>+49 911 55 20 31 41</div>
    <div class="row" style="top:441px"><svg viewBox="0 0 22 22" fill="none" stroke="#a51c45" stroke-width="1"><rect x="6" y="1" width="10" height="20" rx="1"/><path d="M6 4h10M6 18h10"/></svg>+49 170 22 98 17 05</div>
    <div class="row" style="top:487px"><svg viewBox="0 0 22 22" fill="none" stroke="#a51c45" stroke-width="1"><rect x="1" y="5" width="20" height="12"/><path d="M1 5l10 7 10-7"/></svg>info@kelbrotech.eu</div>
  </section>

  <form class="form">
    <div class="field">Vor- und Zuname*</div>
    <div class="field">E-Mail-Adresse*</div>
    <div class="field">Betreff</div>
    <div class="field area">Ihre Nachricht*</div>
    <div class="send">Senden</div>
  </form>

  <section class="map" role="img" aria-label="Stadtplan mit Standortmarkierung der Firma"></section>

  <footer class="footer">
    <div class="about">
      <div class="logo"><span></span>KELBRO</div>
      Viele unterschiedliche Projekte und Kunden durfte Kelbro in den letzten 5 Jahren europaweit betreuen. Mit 11 Jahren Gesamterfahrung im Vellorix KLT Umfeld, ist kein Projekt zu klein oder zu kompliziert für uns.
    </div>
    <div class="col" style="left:537px">
      <h4>Soziale Netzwerke</h4>
      <ul class="social"><li><i></i>Kurznachrichten</li><li><i></i>Netzwerk</li><li><i></i>Karriereprofil</li></ul>
    </div>
    <div class="col links" style="left:654px">
      <h4>Links</h4>
      <a href="#">Home</a><a href="#">Was ist Vellorix KLT?</a><a href="#">Meine Vorteile</a><a href="#" style="border:0">Kontakt</a>
    </div>
    <div class="col contact-col" style="left:770px;width:100px">
      <p>Sie haben Fragen oder möchten einen Termin vereinbaren?</p>
      <p style="font-weight:600">info@kelbrotech.eu</p>
      <p><b>Kelbro GmbH</b><br>Lindenweg 14 - 90411 Nürnberg</p>
    </div>
  </footer>

  <div class="bottom">
    <p>© 2015 - 2018 Kelbro GmbH. <a href="#">Impressum</a> | <a href="#">Datenschutz</a></p>
    <div class="totop"><svg width="10" height="6" viewBox="0 0 10 6" fill="none" stroke="#fff" stroke-width="1.5"><path d="M1 5l4-4 4 4"/></svg></div>
  </div>
</div>
</body>
</html>
```